Building company buisness cards

We are looking for a sharp modern new look for our business cards.We are a New Zealand based company that specialises in house and land packages.We have attached a photo of the current logo and would like to see if it can be improved somehow if needed.We are open to any colours but we have chosen Black and White at this stage. Feel free to change the font and make the logo smarter looking.Play with the colours and see what looks best.We want a card that looks so good know one will want to throw it away!

Target Market(s)

Building profesonals, home buyers

Industry/Entity Type

Building

Contact Information for Business Card

Garrick Tenwood
0275390628
garrickt@hartvale.co.nz

Font styles to use
Serif
Sans Serif

Colors

Designer to choose colors to be used in the design.

Requirements
Must have
• Just the logo on one side and details on the other
• Clean simple looking card
Nice to have
• Round corners and detail like raised or spot UV
• Something that stands out
Should not have
• To title needed, Director etc

```html
<!DOCTYPE html>
<html lang="en">
<head>
<meta charset="utf-8">
<title>Hartvale Business Card</title>
<link rel="stylesheet" href="https://fonts.googleapis.com/css2?family=Montserrat:wght@400;700&display=swap">
<style>
  :root {
    --page-bg: #dcdcdc;
    --card-bg: #2a2b2d;
    --card-edge: #1f2022;
    --ink-light: #f2f2f2;
    --ink-muted: #a9abae;
    --accent-blue: #3b56a3;
    --rule: #8d8f93;
  }
  * { box-sizing: border-box; margin: 0; padding: 0; }
  html, body {
    width: 1200px; height: 1200px; overflow: hidden;
    background: var(--page-bg);
    font-family: "Montserrat", sans-serif;
  }
  .sheet {
    width: 1200px; height: 1200px;
    display: flex; flex-direction: column; align-items: center; justify-content: center;
    gap: 60px;
  }
  .card {
    position: relative;
    width: 840px; height: 480px;
    background: linear-gradient(160deg, #313235 0%, var(--card-bg) 55%, var(--card-edge) 100%);
    border-radius: 18px;
    box-shadow: 0 18px 40px rgba(0,0,0,0.22);
    overflow: hidden;
  }
  /* Front: brand side */
  .card--front {
    display: flex; flex-direction: column; justify-content: center;
    padding-left: 190px;
  }
  .brand__name {
    font-weight: 700; font-size: 92px; letter-spacing: -1px;
    color: var(--ink-light); line-height: 1;
  }
  .brand__tagline {
    margin-top: 18px;
    font-weight: 400; font-size: 30px; letter-spacing: 0.5px;
    color: var(--ink-muted);
  }
  /* Back: details side */
  .mark {
    position: absolute; left: 110px; top: 0; bottom: 0;
    width: 260px;
    display: flex; align-items: center; justify-content: center;
  }
  .mark__name {
    font-weight: 700; font-size: 44px; color: var(--accent-blue);
  }
  .details {
    position: absolute; left: 440px; right: 0; top: 150px;
  }
  .details__name {
    font-weight: 700; font-size: 32px; letter-spacing: 0.5px;
    color: var(--ink-light); text-transform: uppercase;
    white-space: nowrap;
    padding-bottom: 22px;
    border-bottom: 2px solid var(--rule);
  }
  .details__list { list-style: none; margin-top: 24px; }
  .details__list li {
    font-weight: 400; font-size: 24px; line-height: 1.45;
    color: var(--ink-light); white-space: nowrap;
  }
</style>
</head>
<body>
  <main class="sheet">
    <section class="card card--front" aria-label="Card front">
      <span class="brand__name">Hartvale</span>
      <p class="brand__tagline">Houses shaped around you.</p>
    </section>

    <section class="card card--back" aria-label="Card back">
      <div class="mark"><span class="mark__name">Hartvale</span></div>
      <div class="details">
        <h1 class="details__name">Garrick Tenwood</h1>
        <ul class="details__list">
          <li>0275 390 628</li>
          <li>garrickt@hartvale.co.nz</li>
          <li>www.hartvale.co.nz</li>
        </ul>
      </div>
    </section>
  </main>
</body>
</html>
```